The design should look similar to the uploaded example to accommodate the information needed for a business card template. I would like to see the colors orange and charcoal grey incorporated along with the logo.The following should be on the back of the card SPECIALIZING IN NEW AND USED TIRES & WHEELS FOR:- Loaders- Skid Steers- Telehandlers- Boom Lifts- Forklifs and moreELIMINATING DOWNTIMEWheel Exchange Program for New & Used Foam Filled and Solid Rubber TiresSPECIALTY SERVICES- Foam Filling Tires- Largest Tire Press in SE- ONSITE Forklift Tire Press- Boom Truck Services - Rubber Tracks

Target Market(s)

New and Existing Customers

Industry/Entity Type

Business

Contact Information for Business Card

NAMEHEAVY DUTY TIRE, LLC8470 Belvedere RoadWest Palm Beach, FL 33411P: 844-HD-TIRESF: 561-431-6469C:E: W: WWW.GRANITERIMSUPPLY-EXAMPLE.COM

Font styles to use
Sans Serif

Colors
f37122
333333

Requirements
Must have
• The logo and the information indicated for the backside of the card
Nice to have
• Keep the orange and charcoal grey colors

```html
<!DOCTYPE html>
<html lang="en">
<head>
<meta charset="utf-8">
<title>Granite Rim Supply – Business Card</title>
<link rel="stylesheet" href="https://fonts.googleapis.com/css2?family=Rye&family=Open+Sans:wght@400;700&family=Tinos:wght@400;700&display=swap">
<style>
  :root {
    --orange: #f37122;
    --orange-card: #f5873f;
    --charcoal: #333333;
    --charcoal-band: #2f3d3d;
    --phone: #5a3fa6;
    --white: #ffffff;
    --stage: #3a3a3a;
    --mark-faint: rgba(120,120,120,0.14);
  }
  html, body {
    margin: 0;
    padding: 0;
    overflow: hidden;
  }
  body {
    width: 1200px;
    height: 750px;
    background: var(--stage);
    position: relative;
  }
  .card {
    position: absolute;
    top: 215px;
    width: 540px;
    height: 320px;
    overflow: hidden;
    box-shadow: 0 6px 18px rgba(0,0,0,0.35);
  }
  .card-front { left: 40px; background: var(--orange-card); }
  .card-back { left: 620px; background: var(--white); }
  .card-shape {
    position: absolute;
    inset: 0;
    width: 100%;
    height: 100%;
  }

  /* front */
  .company-title {
    position: absolute;
    top: 36px;
    right: 30px;
    margin: 0;
    font-family: "Rye", serif;
    font-weight: 400;
    font-size: 25px;
    letter-spacing: 0.5px;
    color: var(--charcoal-band);
    white-space: nowrap;
  }
  .contact {
    position: absolute;
    top: 82px;
    right: 30px;
    margin: 0;
    text-align: right;
    font-family: "Open Sans", sans-serif;
    font-style: normal;
    color: var(--charcoal);
    font-size: 17px;
    line-height: 1.2;
  }
  .contact .phone {
    color: var(--phone);
    font-size: 22px;
    margin-top: 2px;
  }
  .contact .fax { font-size: 19px; }
  .contact .web { font-size: 18px; }
  .brand-mark {
    position: absolute;
    left: 14px;
    top: 150px;
    display: flex;
    align-items: center;
    gap: 8px;
  }
  .brand-mark .disc {
    width: 64px;
    height: 64px;
    border-radius: 50%;
    background: var(--charcoal-band);
  }
  .brand-mark .brand-name {
    font-family: "Open Sans", sans-serif;
    font-weight: 700;
    font-size: 14px;
    line-height: 1.1;
    color: var(--charcoal-band);
  }

  /* back */
  .specialties {
    position: absolute;
    left: 30px;
    top: 98px;
    font-family: "Tinos", serif;
    color: var(--charcoal);
  }
  .specialties h2 {
    margin: 0 0 12px;
    font-size: 14px;
    font-weight: 700;
    line-height: 1.25;
  }
  .specialties ul, .services ul {
    list-style: none;
    margin: 0;
    padding: 0;
    font-size: 14px;
    line-height: 25px;
  }
  .services {
    position: absolute;
    right: 30px;
    top: 98px;
    text-align: right;
    font-family: "Tinos", serif;
    color: var(--charcoal);
  }
  .services h2 {
    margin: 0 0 6px;
    font-size: 13px;
    font-weight: 700;
    line-height: 1.25;
  }
  .services h3 {
    margin: 0;
    font-size: 14px;
    font-weight: 400;
    line-height: 25px;
  }
  .faint-mark {
    position: absolute;
    left: 200px;
    top: 245px;
    width: 150px;
    height: 150px;
    border-radius: 50%;
    background: var(--mark-faint);
  }
</style>
</head>
<body>

<section class="card card-front" aria-label="Business card front">
  <svg class="card-shape" viewBox="0 0 540 320" preserveAspectRatio="none" aria-hidden="true">
    <polygon points="0,262 163,242 540,318 540,320 0,320" fill="var(--white)"/>
    <polygon points="0,255 163,234 540,310 540,320 163,243 0,264" fill="var(--charcoal-band)"/>
  </svg>
  <h1 class="company-title">GRANITE RIM SUPPLY LLC</h1>
  <address class="contact">
    <div>5126 Marston Lane</div>
    <div>Coral Haven, FL 33290</div>
    <div class="phone">P: 844-GR-WHEEL</div>
    <div class="fax">F: 561-278-9053</div>
    <div class="web">www.graniterimsupply-example.com</div>
  </address>
  <div class="brand-mark">
    <span class="disc"></span>
    <span class="brand-name">GRANITE<br>RIM</span>
  </div>
</section>

<section class="card card-back" aria-label="Business card back">
  <svg class="card-shape" viewBox="0 0 540 320" preserveAspectRatio="none" aria-hidden="true">
    <polygon points="181,0 540,0 540,320 388,320" fill="var(--orange-card)"/>
  </svg>
  <div class="faint-mark"></div>
  <div class="specialties">
    <h2>specializing in new and<br>used tires &amp; wheels for:</h2>
    <ul>
      <li>Loaders</li>
      <li>Skid Steers</li>
      <li>Telehandlers</li>
      <li>Boom Lifts</li>
      <li>Forklifs and more</li>
    </ul>
  </div>
  <div class="services">
    <h2>Wheel Exchange Program for New &amp;<br>Used Foam Filled and Solid Rubber Tires</h2>
    <h3>SPECIALTY SERVICES</h3>
    <ul>
      <li>Foam Filling Tires</li>
      <li>Largest Tire Press in SE</li>
      <li>ONSITE Forklift Tire Press</li>
      <li>Boom Truck Services</li>
      <li>Rubber Tracks</li>
    </ul>
  </div>
</section>

</body>
</html>
```